Flag Order

We were just looking to order some branding flags to put on our rental equipment for our business. We would like different examples of the colors, shapes, sizes, backgrounds etc. Was thinking of just doing the plains icon instead of the whole logo on there. but open to ideas. preferably not a white background as they could get dirty,

```html
<!DOCTYPE html>
<html lang="en">
<head>
<meta charset="utf-8">
<title>Ridge Equipment Rentals – Flag Concepts</title>
<link rel="stylesheet" href="https://fonts.googleapis.com/css2?family=Michroma&family=Montserrat:wght@500&display=swap">
<style>
  :root {
    --page: #ffffff;
    --flag: #000000;
    --ink: #ffffff;
    --label: #8a8a8a;
    --steel: #b9bcc0;
    --steel-dark: #6d7075;
    --pole: #111111;
  }
  html, body {
    margin: 0;
    padding: 0;
    width: 1200px;
    height: 800px;
    overflow: hidden;
    background: var(--page);
  }
  .board { display: block; width: 1200px; height: 800px; }
  .design-label {
    font-family: "Montserrat", sans-serif;
    font-weight: 500;
    font-size: 11px;
    letter-spacing: 4px;
    fill: var(--label);
  }
  .flag-cloth { fill: var(--flag); }
  .pole { fill: var(--pole); }
  .pole-cap { fill: var(--pole); }
  .brand-name, .brand-line {
    font-family: "Michroma", sans-serif;
    fill: var(--ink);
  }
  .brand-mark { fill: var(--ink); }
  .stand-leg { stroke: var(--steel-dark); stroke-width: 1.6; fill: none; }
  .stand-hub { fill: var(--steel); stroke: var(--steel-dark); stroke-width: 1; }
  .stand-post { fill: var(--pole); }
</style>
</head>
<body>
<svg class="board" viewBox="0 0 1200 800" xmlns="http://www.w3.org/2000/svg">
  <defs>
    <g id="ground-stand">
      <rect class="stand-post" x="-3" y="-58" width="6" height="50"/>
      <rect class="stand-hub" x="-4" y="-60" width="8" height="6"/>
      <line class="stand-leg" x1="0" y1="0" x2="-65" y2="12"/>
      <line class="stand-leg" x1="0" y1="0" x2="48" y2="-9"/>
      <line class="stand-leg" x1="0" y1="0" x2="-42" y2="44"/>
      <line class="stand-leg" x1="0" y1="0" x2="70" y2="26"/>
      <rect class="stand-hub" x="-6" y="-10" width="12" height="14" rx="2"/>
    </g>
  </defs>

  <!-- Design 1: tall feather banner -->
  <text class="design-label" x="160" y="60" text-anchor="middle">DESIGN #1</text>
  <g class="flag flag--feather">
    <rect class="flag-cloth" x="92" y="96" width="148" height="561"/>
    <rect class="flag-cloth" x="88" y="98" width="8" height="6" rx="3"/>
    <text class="brand-name" transform="translate(184 500) rotate(-90)" font-size="60">RIDGE</text>
    <text class="brand-line" transform="translate(212 500) rotate(-90)" font-size="17.5" letter-spacing="6.5">EQUIPMENT RENTALS</text>
    <rect class="brand-mark" x="136" y="545" width="60" height="60"/>
  </g>
  <use href="#ground-stand" x="96" y="715"/>

  <!-- Design 2: rectangle flag, name -->
  <text class="design-label" x="437" y="60" text-anchor="middle">DESIGN #2</text>
  <g class="flag flag--pole">
    <rect class="pole" x="294" y="104" width="7" height="560"/>
    <circle class="pole-cap" cx="297" cy="102" r="7"/>
    <rect class="flag-cloth" x="300" y="113" width="276" height="167"/>
    <rect class="brand-mark" x="416" y="146" width="46" height="46"/>
    <text class="brand-name" x="436" y="248" text-anchor="middle" font-size="27">RIDGE</text>
    <text class="brand-line" x="436" y="265" text-anchor="middle" font-size="7" letter-spacing="2">EQUIPMENT RENTALS</text>
  </g>
  <use href="#ground-stand" x="297" y="715"/>

  <!-- Design 3: rectangle flag, short mark -->
  <text class="design-label" x="757" y="60" text-anchor="middle">DESIGN #3</text>
  <g class="flag flag--pole">
    <rect class="pole" x="610" y="104" width="7" height="560"/>
    <circle class="pole-cap" cx="613" cy="102" r="7"/>
    <rect class="flag-cloth" x="617" y="113" width="274" height="167"/>
    <rect class="brand-mark" x="670" y="176" width="40" height="40"/>
    <text class="brand-name" x="722" y="212" font-size="36">RIDGE</text>
  </g>
  <use href="#ground-stand" x="613" y="715"/>

  <!-- Design 4: small banner, name -->
  <text class="design-label" x="845" y="378" text-anchor="middle">DESIGN #4</text>
  <g class="flag flag--small">
    <rect class="flag-cloth" x="771" y="417" width="148" height="237"/>
    <rect class="flag-cloth" x="768" y="419" width="8" height="6" rx="3"/>
    <rect class="brand-mark" x="822" y="478" width="46" height="46"/>
    <text class="brand-name" x="846" y="598" text-anchor="middle" font-size="24">RIDGE</text>
    <text class="brand-line" x="846" y="608" text-anchor="middle" font-size="6.2" letter-spacing="1.6">EQUIPMENT RENTALS</text>
  </g>
  <use href="#ground-stand" x="774" y="715"/>

  <!-- Design 5: small banner, short mark -->
  <text class="design-label" x="1086" y="378" text-anchor="middle">DESIGN #5</text>
  <g class="flag flag--small">
    <rect class="flag-cloth" x="1013" y="417" width="147" height="237"/>
    <rect class="flag-cloth" x="1010" y="419" width="8" height="6" rx="3"/>
    <rect class="brand-mark" x="1066" y="490" width="40" height="40"/>
    <text class="brand-name" x="1086" y="572" text-anchor="middle" font-size="26">RIDGE</text>
  </g>
  <use href="#ground-stand" x="1016" y="715"/>
</svg>
</body>
</html>
```